Design and Renovation Company Luxury Business Card

I want to create a luxury business card for a Design and Renovation Firm . We will use our current logo. The company name is 528BUILDA. We do not want anything standard. We need a very unique concept.
Please see uploaded inspiration. I really like the textured paper option. I would like the card to be thick with debossing, and/or embossing options. The logo has orange in it but I would like to see the card with and without the orange. I think the orange may make the company feel less high-end. The goal is to elevate the logo not match its vibe per se of the logo. We want something very unique, not standard at all!
I would like a space for :
Logo,
Name,
Position,
Email,
Office number,
Website Address,
Business Address,
Thank you!
Have fun!
Target Market(s)
Home owners Age 35 +
Industry/Entity Type
Design and Renovation
Contact Information for Business Card
Logo, Name, Position, Email, Office number, Website Address, Business Address,.
Colors
Designer to choose colors to be used in the design.
Requirements
Must have
- A luxury designer feel. Must be black or dark grey but open to other luxury ideas.
Nice to have
- Gold, silver, black embossing or debossing. Textured paper design.
Should not have
- A cheap look and feel.

```html
<!DOCTYPE html>
<html lang="en">
<head>
<meta charset="utf-8">
<title>528BUILDA Business Card</title>
<link href="https://fonts.googleapis.com/css2?family=Arimo:wght@400;700&display=swap" rel="stylesheet">
<style>
  :root {
    --backdrop: #d4d4d4;
    --orange: #e58a1c;
    --charcoal: #2f2f2f;
    --white: #f6f6f6;
    --muted: #cfcfcf;
  }
  * { box-sizing: border-box; margin: 0; padding: 0; }
  html, body { width: 1200px; height: 800px; overflow: hidden; }
  body {
    background: var(--backdrop);
    font-family: "Arimo", Arial, sans-serif;
    position: relative;
  }
  .card {
    position: absolute;
    width: 540px;
    height: 309px;
    border-radius: 18px;
    overflow: hidden;
    box-shadow: 0 10px 28px rgba(0,0,0,0.22);
  }
  .card-front { left: 40px; top: 245px; background: var(--orange); color: var(--white); }
  .card-back { left: 620px; top: 245px; background: var(--charcoal); color: var(--white); }

  .front-band {
    position: absolute; left: 250px; right: 0; bottom: 0; height: 12px;
    background: var(--charcoal);
  }
  .front-brand {
    position: absolute; top: 40px; right: 32px;
    display: flex; align-items: center; gap: 10px;
  }
  .front-brand-square { width: 22px; height: 22px; background: var(--white); flex: none; }
  .front-brand-name { font-weight: 700; font-size: 18px; color: var(--white); }

  .front-rule {
    position: absolute; left: 32px; right: 32px; top: 196px;
    height: 1px; background: rgba(255,255,255,0.75);
  }
  .person { position: absolute; left: 32px; top: 144px; }
  .person-name { font-weight: 700; font-size: 23px; line-height: 1.1; }
  .person-role { font-size: 13px; margin-top: 2px; }

  .contacts { position: absolute; left: 32px; top: 208px; list-style: none; }
  .contacts li {
    display: flex; align-items: center; gap: 8px;
    font-size: 13px; line-height: 19px;
  }
  .contacts svg { width: 11px; height: 11px; fill: var(--white); flex: none; }

  .address {
    position: absolute; right: 32px; top: 208px;
    text-align: right; font-size: 13px; line-height: 19px;
  }

  .brand {
    position: absolute; left: 0; right: 0; top: 118px;
    display: flex; flex-direction: column; align-items: center;
  }
  .brand-row { display: flex; align-items: center; gap: 14px; }
  .brand-square { width: 30px; height: 30px; background: var(--white); flex: none; }
  .brand-name { font-weight: 700; font-size: 34px; color: var(--white); }
  .brand-url { font-size: 13px; color: var(--muted); margin-top: 12px; }
</style>
</head>
<body>
  <section class="card card-front" aria-label="Card front">
    <div class="front-brand">
      <span class="front-brand-square" aria-hidden="true"></span>
      <span class="front-brand-name">528BUILDA</span>
    </div>
    <div class="person">
      <p class="person-name">Marcus Hale</p>
      <p class="person-role">President</p>
    </div>
    <div class="front-rule"></div>
    <ul class="contacts">
      <li>
        <svg viewBox="0 0 24 24" aria-hidden="true"><path d="M6.6 10.8a15.1 15.1 0 0 0 6.6 6.6l2.2-2.2c.3-.3.7-.4 1-.2 1.1.4 2.3.6 3.6.6.6 0 1 .4 1 1V20c0 .6-.4 1-1 1A17 17 0 0 1 3 4c0-.6.4-1 1-1h3.5c.6 0 1 .4 1 1 0 1.3.2 2.5.6 3.6.1.3 0 .7-.2 1z"/></svg>
        (555) 0142-7788
      </li>
      <li>
        <svg viewBox="0 0 24 24" aria-hidden="true"><path d="M2 5h20v14H2z M3 6l9 7 9-7"/></svg>
        name@528BUILDA.com
      </li>
      <li>
        <svg viewBox="0 0 24 24" aria-hidden="true"><circle cx="12" cy="12" r="10"/></svg>
        www.528BUILDA.com
      </li>
    </ul>
    <p class="address">4127 Harrow Lane<br>Glen Oaks, NY 10490</p>
    <div class="front-band"></div>
  </section>

  <section class="card card-back" aria-label="Card back">
    <div class="brand">
      <div class="brand-row">
        <span class="brand-square" aria-hidden="true"></span>
        <p class="brand-name">528BUILDA</p>
      </div>
      <p class="brand-url">www.528BUILDA.com</p>
    </div>
  </section>
</body>
</html>
```